Etikett für Rotweinflasche
Liebe farbkosmos Atelier, wir werden uns bei der endgültigen Etikettengestaltung (finale Größe + Rückseite) noch an Euch melden. Bitte sendet uns euren Kontakt an helga.brandt@morvelli.wine
Zielgruppe
Morvelli Italia ist ein exklusives Boutique-Weingut in Sizilien, das hochqualitative Spitzenweine in kleinen Mengen mit modernster Technologie und stets nachhaltig erzeugt. Wir hinterfragen sowohl in der Agronomie im Weingarten als auch in der Önologie im Weinkeller alle herrschenden Traditionen und trachten danach, stets das beste Endprodukt zu kreieren. Der vulkanische, kalkreiche Boden Siziliens sowie trockene, sonnenreiche und niederschlagsarme Vegetationsperioden sind unsere optimale Basis.
Zielgruppe: Internationale Genussmenschen jeglichen Alters, die sich bewusst auch höherpreisige Weine (um die €30+) gönnen , vor allem kunstaffine young professionals mit Qualitäts-& Nachhaltigkeitsanspruch
Aufgabenstellung
Das Etikett ist für Rotwein-Flaschen (Cabernet Sauvignon / Nero D'Avola / Frappato / Syrah / Cerasuolo / Petit Verdot / sowie einen Bourdeaux-Cuveè aus Cabernet Sauvignon und Petit Verdot) .
Die Flasche ist reinschwarz, sehr hochwertig und schwer.
Flaschenform: Bordeauxflasche siehe technisches Datenblatt
Sleeve über dem Korken: schwarz mit weißer Schrift wie bisher
Zu gestalten ist das Etikett der Vorderseite. Zumindest die jeweilige Rotwein-Sorte ist auch textlich darzustellen (zwecks Scannen mit Trubel-App)
Der Kreativität kann freien Lauf gelassen werden! Unterscheidbarkeit vom Markt ist explizit gewollt.
Unsere aktuellen Etiketten und Markenauftritt siehe: https://morvelli.wine/shop/

```html
<!DOCTYPE html>
<html lang="de">
<head>
<meta charset="utf-8">
<title>Morvelli Italia – Rotwein-Etiketten</title>
<link rel="stylesheet" href="https://fonts.googleapis.com/css2?family=Anton&family=Barlow+Condensed:ital,wght@1,500&display=swap">
<style>
  :root {
    --backdrop: #c9c9c1;
    --glow-red: #d93a2b;
    --glow-red-soft: #c23a2e;
    --edge-nero: #2b2423;
    --edge-cabernet: #2f5f97;
    --edge-verdot: #4d6e47;
    --variety-pink: #f2a08f;
    --small-white: #f1e9e6;
    --doc-red: #e0302a;
  }
  * { box-sizing: border-box; margin: 0; padding: 0; }
  html, body {
    width: 1200px; height: 900px; overflow: hidden;
    background: var(--backdrop);
  }
  .label-row {
    width: 1200px; height: 900px;
    display: flex; justify-content: center; align-items: center; gap: 60px;
  }
  .label {
    position: relative;
    width: 300px; height: 480px;
    overflow: hidden;
  }
  .label__glow {
    position: absolute; inset: 0;
  }
  .label--nero .label__glow {
    background: radial-gradient(ellipse 62% 58% at 45% 45%, var(--glow-red) 0%, var(--glow-red-soft) 38%, var(--edge-nero) 100%);
  }
  .label--cabernet .label__glow {
    background: radial-gradient(ellipse 55% 50% at 40% 40%, var(--glow-red) 0%, #a84a5c 40%, var(--edge-cabernet) 100%);
  }
  .label--verdot .label__glow {
    background: radial-gradient(ellipse 62% 58% at 45% 45%, var(--glow-red) 0%, var(--glow-red-soft) 40%, var(--edge-verdot) 100%);
  }
  .label__vintage {
    position: absolute; top: 20px; right: 22px;
    font-family: "Barlow Condensed", sans-serif; font-style: italic; font-weight: 500;
    font-size: 17px; letter-spacing: 1px; color: var(--small-white);
  }
  .label__origin {
    position: absolute; bottom: 24px; right: 22px;
    font-family: "Barlow Condensed", sans-serif; font-style: italic; font-weight: 500;
    font-size: 18px; letter-spacing: 2px; color: var(--small-white);
  }
  .label__origin .doc { color: var(--doc-red); }
  .label__variety {
    position: absolute; top: 50%; right: 30px;
    transform: translateY(-50%) rotate(180deg);
    writing-mode: vertical-rl;
    font-family: "Anton", sans-serif;
    font-size: 46px; line-height: 1.02; letter-spacing: 0.5px;
    text-transform: uppercase; text-align: center;
    color: var(--variety-pink);
  }
  .label--cabernet .label__variety { font-size: 40px; }
</style>
</head>
<body>
  <main class="label-row">
    <article class="label label--nero">
      <div class="label__glow" role="img" aria-label="Weiches rotes Leuchten auf dunklem Grund mit verstreuten hellen Kieselformen"></div>
      <span class="label__vintage">2019</span>
      <h2 class="label__variety">Nero<br>D'Avola</h2>
      <p class="label__origin">SICILIA <span class="doc">DOC</span></p>
    </article>

    <article class="label label--cabernet">
      <div class="label__glow" role="img" aria-label="Weiches rotes Leuchten auf blauem Grund mit verstreuten hellen Kieselformen"></div>
      <span class="label__vintage">2019</span>
      <h2 class="label__variety">Cabernet<br>Sauvignon</h2>
      <p class="label__origin">SICILIA <span class="doc">DOC</span></p>
    </article>

    <article class="label label--verdot">
      <div class="label__glow" role="img" aria-label="Weiches rotes Leuchten auf grünem Grund mit verstreuten hellen Kieselformen"></div>
      <span class="label__vintage">2019</span>
      <h2 class="label__variety">Petit<br>Verdot</h2>
      <p class="label__origin">SICILIA <span class="doc">DOC</span></p>
    </article>
  </main>
</body>
</html>
```